Digital Marketing Agency Landing Page

At VELIM, we offer a comprehensive solution for solar companies' client acquisition needs in the rapidly growing industry. We handle end-to-end client acquisition, meaning we manage the entire lifecycle of capturing new clients—from initial lead generation to delivering the ready-to-buy homeowner. Our expertise in targeted advertising, data analytics, and customer relationship management ensures that we not only find potential customers but also nurture them through tailored engagement strategies until they are ready to make a purchase. By entrusting us with your client acquisition process, solar companies can focus on what they do best—providing sustainable energy solutions—while we work behind the scenes to grow your customer base and increase your market share.

We need to restructure our website to make it more professional. We don't need any complex functionalities. We are looking for someone that is good in design and can build a visually aesthetic website following our brand image. We only need a landing page and a lead form in the end. I would like to have only one page, but a relatively big one where people scroll down. I would like to have a minimal and classy look. Something that is timeless and elegant.

Structure:

initial page
About us
How we operate
Get in touch

Target Market(s)

Solar Comapanies

Industry/Entity Type

Marketing solautions

Coding

Coded - Design and coding required

Number of Pages Required

1 page

Requirements
Nice to have
• Inspirations: https://www.qz.zu/ https://www.marchbeck.example/ https://www.tovanrid.example/ https://pruvo.example/

```html
<!DOCTYPE html>
<html lang="en">
<head>
<meta charset="utf-8">
<title>VELIM — Client Acquisition for Solar Companies</title>
<link rel="stylesheet" href="https://fonts.googleapis.com/css2?family=Montserrat:wght@300;400&family=Roboto:wght@400;500;700&display=swap">
<style>
:root{
  --navy:#102431;
  --navy-band:#1e3545;
  --ink:#1b1b1b;
  --text:#5c6670;
  --field:#eef1f4;
  --field-text:#8b939b;
  --white:#ffffff;
  --footer:#0e0e0f;
  --footer-text:#e6e6e6;
  --hero-a:#8a6a4c;
  --hero-b:#b99a78;
  --hero-c:#6f7f8e;
}
*{box-sizing:border-box;margin:0;padding:0}
html,body{width:1200px;height:2211px;overflow:hidden;background:var(--white)}
body{font-family:'Roboto',sans-serif;color:var(--ink)}
.page{position:relative;width:1200px;height:2211px;overflow:hidden}
.abs{position:absolute}
.heading{font-family:'Montserrat',sans-serif;font-weight:300;letter-spacing:1px}

/* top bar */
.topbar{left:0;top:0;width:1200px;height:31px;background:var(--navy);color:var(--white);font-size:13px}
.topbar .social{left:144px;top:6px;display:flex;gap:9px}
.topbar .social span{width:19px;height:19px;border-radius:50%;background:var(--white);opacity:.9}
.topbar .phone{left:542px;top:8px;display:flex;align-items:center;gap:6px}
.topbar .mail{right:144px;top:7px;display:flex;align-items:center;gap:6px}

/* nav */
.nav{left:0;top:31px;width:1200px;height:65px;font-size:14px;font-weight:500}
.nav a{position:absolute;top:26px;color:var(--ink);text-decoration:none}
.nav .sep{position:absolute;top:4px;width:1px;height:60px;background:#e5e7ea}
.brand{left:537px;top:6px;width:125px;height:54px;background:var(--navy);display:flex;align-items:center;justify-content:center}
.brand span{border:1px solid var(--white);padding:2px 6px;color:var(--white);font-family:'Montserrat',sans-serif;font-weight:300;font-size:24px;letter-spacing:1px}
.btn{position:absolute;background:var(--navy);color:var(--white);font-weight:500;display:flex;align-items:center;justify-content:center;gap:6px;white-space:nowrap}
.btn::before{content:"";position:absolute;left:-7px;top:-6px;width:88%;height:100%;border:1px solid var(--navy);border-right:none;border-bottom:none}
.btn.light::before{border-color:var(--white)}
.circ-arrow{width:13px;height:13px}

/* hero */
.frame{border:3px solid var(--navy)}
.hero-img{left:38px;top:109px;width:1122px;height:614px;background:linear-gradient(135deg,var(--hero-c) 0%,var(--hero-a) 35%,var(--hero-b) 60%,var(--hero-a) 85%,var(--hero-c) 100%)}
.hero-shade{left:38px;top:109px;width:1122px;height:614px;background:linear-gradient(90deg,rgba(20,20,20,.35),rgba(20,20,20,.05))}
.hero-title{left:144px;top:305px;color:var(--white);font-size:54px}
.hero-lead{left:144px;top:372px;width:440px;color:var(--white);font-size:16px;font-weight:500;line-height:24px}

.quote{left:674px;top:213px;width:380px;height:410px;background:var(--white);border-top:3px solid var(--navy)}
.quote h2{position:absolute;left:0;top:27px;width:100%;text-align:center;font-size:18px;color:var(--ink)}
.quote p{position:absolute;left:0;top:58px;width:100%;text-align:center;font-size:12.5px;color:var(--text)}
.field{position:absolute;height:40px;background:var(--field);color:var(--field-text);font-size:12px;padding-left:12px;display:flex;align-items:center}

/* about */
.about-img{left:144px;top:816px;width:421px;height:321px;background:linear-gradient(120deg,#3a5168 0%,#8fa3b5 45%,#d9dde2 70%,#5d6f80 100%)}
.about-title{left:639px;top:826px;font-size:38px;color:var(--ink)}
.about-copy{left:639px;top:885px;width:417px;font-size:13.5px;line-height:21.5px;color:var(--text);text-align:justify}
.about-copy p+p{margin-top:10px}

/* services */
.band{left:38px;top:1250px;width:1122px;height:303px;background:var(--navy-band)}
.services-title{left:0;top:1304px;width:1200px;text-align:center;color:var(--white);font-size:38px}
.card{position:absolute;top:1382px;width:289px;background:var(--white);box-shadow:0 4px 14px rgba(0,0,0,.08);text-align:center}
.card .pic{position:absolute;left:4px;top:4px;width:281px;height:194px}
.card .icon{position:absolute;left:113px;top:165px;width:63px;height:64px;background:var(--navy);display:flex;align-items:center;justify-content:center}
.card h3{position:absolute;left:10px;top:248px;width:269px;font-size:17px;line-height:22px;color:var(--ink)}
.card .txt{position:absolute;left:16px;width:257px;font-size:13.5px;line-height:22px;color:var(--text)}
.card .more{position:absolute;left:0;width:100%;font-size:13.5px;font-weight:700;color:var(--navy);display:flex;justify-content:center;align-items:center;gap:6px}

/* footer */
.footer{left:38px;top:1860px;width:1122px;height:351px;background:var(--footer)}
.f-brand{left:146px;top:1965px;width:159px;height:60px;border:1px solid #c9ccd0;display:flex;align-items:center;justify-content:center}
.f-brand span{border:1px solid #c9ccd0;padding:3px 10px;color:var(--white);font-family:'Montserrat',sans-serif;font-weight:300;font-size:32px;letter-spacing:1px}
.f-social{left:174px;top:2049px;display:flex;gap:14px}
.f-social span{width:14px;height:14px;border-radius:50%;background:var(--white)}
.f-col h4{color:var(--white);font-size:15.5px;font-weight:500}
.f-col{color:var(--footer-text);font-size:13px}
.f-item{position:absolute;left:0;display:flex;gap:8px}
.f-item b{display:block;font-size:11px;font-weight:700;color:var(--white)}
.f-links div{position:absolute;left:0}
.divider{left:144px;top:2132px;width:840px;border-top:1px dashed #3a3a3a}
.goup{left:987px;top:2121px;width:67px;height:19px;background:var(--navy);color:var(--white);font-size:11px;font-weight:700;display:flex;align-items:center;justify-content:center;gap:4px}
.goup::before{content:"";position:absolute;left:-4px;top:-5px;width:60px;height:10px;border:1px solid var(--white);border-bottom:none;border-right:none}
.copy{left:144px;top:2164px;color:var(--footer-text);font-size:13px}
.legal{left:750px;top:2164px;color:var(--footer-text);font-size:13px}
</style>
</head>
<body>
<div class="page">

  <!-- top bar -->
  <div class="abs topbar">
    <div class="abs social"><span></span><span></span><span></span><span></span></div>
    <div class="abs phone">
      <svg width="11" height="11" viewBox="0 0 24 24"><path fill="#fff" d="M6.6 10.8a15 15 0 006.6 6.6l2.2-2.2c.3-.3.7-.4 1-.2 1.1.4 2.3.6 3.6.6.6 0 1 .4 1 1V20c0 .6-.4 1-1 1A17 17 0 013 4c0-.6.4-1 1-1h3.5c.6 0 1 .4 1 1 0 1.3.2 2.5.6 3.6.1.3 0 .7-.2 1z"/></svg>
      +1 555 014 2290
    </div>
    <div class="abs mail">
      <svg width="13" height="10" viewBox="0 0 26 20"><rect width="26" height="20" rx="2" fill="#fff"/><path d="M1 2l12 9 12-9" stroke="#102431" stroke-width="2" fill="none"/></svg>
      hello@velim.example
    </div>
  </div>

  <!-- navigation -->
  <nav class="abs nav">
    <a style="left:144px">HOME</a>
    <span class="sep" style="left:210px"></span>
    <a style="left:239px">ABOUT US</a>
    <span class="sep" style="left:337px"></span>
    <a style="left:360px">OUR SERVICES</a>
    <div class="abs brand"><span>VELIM</span></div>
    <a style="left:699px">CLIENTS</a>
    <span class="sep" style="left:778px"></span>
    <a style="left:799px">CONTACT US</a>
    <div class="btn" style="left:941px;top:16px;width:113px;height:37px;font-size:12px">
      <svg width="11" height="11" viewBox="0 0 24 24"><path d="M4 20V6h8M20 4L10 14l-1 3 3-1L22 6z" stroke="#fff" stroke-width="2" fill="none"/></svg>
      GET A QUOTE
    </div>
  </nav>

  <!-- hero -->
  <div class="abs frame" style="left:60px;top:100px;width:1080px;height:638px"></div>
  <div class="abs frame" style="left:26px;top:135px;width:1149px;height:557px"></div>
  <div class="abs hero-img" role="img" aria-label="Team working together at a wooden desk, seen from above"></div>
  <div class="abs hero-shade"></div>
  <h1 class="abs heading hero-title">VELIM</h1>
  <p class="abs hero-lead">Lorem ipsum dolor sit amet, consectetur adipiscing elit, sed do eiusmod tempor incididunt ut labore et.</p>
  <div class="btn light" style="left:151px;top:439px;width:136px;height:38px;font-size:14.5px">
    GET STARTED
    <svg class="circ-arrow" viewBox="0 0 16 16"><circle cx="8" cy="8" r="8" fill="#fff"/><path d="M5 8h6M8.5 5l3 3-3 3" stroke="#102431" stroke-width="1.8" fill="none"/></svg>
  </div>

  <section class="abs quote">
    <h2 class="heading">GET A QUOTE TODAY</h2>
    <p>Lorem ipsum dolor sit amet, consectetur adipiscing elit</p>
    <div class="field" style="left:22px;top:90px;width:160px">Your Name</div>
    <div class="field" style="left:193px;top:90px;width:163px">Telephone</div>
    <div class="field" style="left:22px;top:142px;width:334px">Phone Number</div>
    <div class="field" style="left:22px;top:194px;width:334px">Email Address</div>
    <div class="field" style="left:22px;top:246px;width:334px">Location</div>
    <div class="btn" style="left:92px;top:332px;width:199px;height:42px;font-size:15px">REQUEST CALL BACK</div>
  </section>

  <!-- about -->
  <div class="abs frame" style="left:127px;top:843px;width:410px;height:309px;border-width:2px"></div>
  <div class="abs about-img" role="img" aria-label="Business partners shaking hands in a modern office"></div>
  <h2 class="abs heading about-title">ABOUT US</h2>
  <div class="abs about-copy">
    <p>Lorem ipsum dolor sit amet, consectetur adipiscing elit, sed do eiusmod tempor incididunt ut labore et dolore magna aliqua. Ut enim ad minim veniam, quis nostrud exercitation ullamco.</p>
    <p>Sed ut perspiciatis unde omnis iste natus error sit voluptatem accusantium doloremque laudantium, totam rem aperiam, eaque ipsa quae ab illo inventore veritatis et quasi architecto beatae vitae dicta sunt explicabo. Nemo enim ipsam voluptatem quia voluptas sit aspernatur aut odit aut fugit, sed quia consequuntur.</p>
  </div>
  <div class="btn" style="left:645px;top:1099px;width:137px;height:36px;font-size:14.5px">
    LEARN MORE
    <svg class="circ-arrow" viewBox="0 0 16 16"><circle cx="8" cy="8" r="8" fill="#fff"/><path d="M5 8h6M8.5 5l3 3-3 3" stroke="#102431" stroke-width="1.8" fill="none"/></svg>
  </div>

  <!-- services -->
  <div class="abs frame" style="left:60px;top:1232px;width:1080px;height:60px;border-bottom:none"></div>
  <div class="abs band"></div>
  <h2 class="abs heading services-title">OUR SERVICES</h2>

  <article class="card" style="left:144px;height:376px">
    <div class="pic" role="img" aria-label="Analyst reviewing charts on a laptop" style="background:linear-gradient(135deg,#c9d2dc,#5a7a98 60%,#2f4358)"></div>
    <div class="icon"><svg width="30" height="30" viewBox="0 0 30 30" fill="none" stroke="#fff" stroke-width="1.5"><rect x="3" y="3" width="24" height="20"/><path d="M8 19v-5M13 19v-9M18 19v-7M23 19V8M10 27h10"/></svg></div>
    <h3 class="heading">DATA ANALYTICS</h3>
    <p class="txt" style="top:280px">Lorem ipsum dolor sit amet, consectetur adipiscing elit, sed do eiusmod</p>
    <div class="more" style="top:340px">READ MORE <svg class="circ-arrow" viewBox="0 0 16 16"><circle cx="8" cy="8" r="8" fill="#102431"/><path d="M5 8h6M8.5 5l3 3-3 3" stroke="#fff" stroke-width="1.8" fill="none"/></svg></div>
  </article>

  <article class="card" style="left:456px;height:390px">
    <div class="pic" role="img" aria-label="Glowing network of customer connections held in a hand" style="background:radial-gradient(circle at 50% 45%,#9fc3cf 0%,#3c6574 35%,#1f3440 80%)"></div>
    <div class="icon"><svg width="30" height="30" viewBox="0 0 30 30" fill="none" stroke="#fff" stroke-width="1.5"><circle cx="15" cy="8" r="4"/><circle cx="6" cy="21" r="3"/><circle cx="15" cy="21" r="3"/><circle cx="24" cy="21" r="3"/><path d="M15 12v6M15 15l-9 3M15 15l9 3"/></svg></div>
    <h3 class="heading">CUSTOMER RELATIONSHIP MANAGEMEN</h3>
    <p class="txt" style="top:297px">Lorem ipsum dolor sit amet, consectetur adipiscing elit, sed do eiusmod</p>
    <div class="more" style="top:358px">READ MORE <svg class="circ-arrow" viewBox="0 0 16 16"><circle cx="8" cy="8" r="8" fill="#102431"/><path d="M5 8h6M8.5 5l3 3-3 3" stroke="#fff" stroke-width="1.8" fill="none"/></svg></div>
  </article>

  <article class="card" style="left:766px;height:376px">
    <div class="pic" role="img" aria-label="Hand touching a digital globe of connected audiences" style="background:radial-gradient(circle at 60% 40%,#d5dde2 0%,#6d8b99 40%,#1e3a4a 90%)"></div>
    <div class="icon"><svg width="30" height="30" viewBox="0 0 30 30" fill="none" stroke="#fff" stroke-width="1.5"><path d="M4 12h5l10-6v18L9 18H4zM9 18l2 7"/><circle cx="25" cy="9" r="2"/><circle cx="25" cy="15" r="2"/><circle cx="25" cy="21" r="2"/></svg></div>
    <h3 class="heading">ADVERTISING</h3>
    <p class="txt" style="top:280px">Lorem ipsum dolor sit amet, consectetur adipiscing elit, sed do eiusmod</p>
    <div class="more" style="top:340px">READ MORE <svg class="circ-arrow" viewBox="0 0 16 16"><circle cx="8" cy="8" r="8" fill="#102431"/><path d="M5 8h6M8.5 5l3 3-3 3" stroke="#fff" stroke-width="1.8" fill="none"/></svg></div>
  </article>

  <!-- footer -->
  <div class="abs frame" style="left:60px;top:1849px;width:1080px;height:40px;border-bottom:none"></div>
  <div class="abs frame" style="left:26px;top:1888px;width:1149px;height:296px"></div>
  <footer class="abs footer"></footer>
  <div class="abs f-brand"><span>VELIM</span></div>
  <div class="abs f-social"><span></span><span></span><span></span><span></span></div>

  <div class="abs f-col" style="left:384px;top:1928px;width:250px">
    <h4>Our Office Address</h4>
    <div class="f-item" style="top:41px"><svg width="12" height="12" viewBox="0 0 24 24"><path fill="#fff" d="M6.6 10.8a15 15 0 006.6 6.6l2.2-2.2c.3-.3.7-.4 1-.2 1.1.4 2.3.6 3.6.6.6 0 1 .4 1 1V20c0 .6-.4 1-1 1A17 17 0 013 4c0-.6.4-1 1-1h3.5c.6 0 1 .4 1 1 0 1.3.2 2.5.6 3.6.1.3 0 .7-.2 1z"/></svg><div><b>Phone</b>+1-555-014-2290</div></div>
    <div class="f-item" style="top:89px"><svg width="13" height="10" viewBox="0 0 26 20" style="margin-top:2px"><rect width="26" height="20" rx="2" fill="#fff"/><path d="M1 2l12 9 12-9" stroke="#0e0e0f" stroke-width="2" fill="none"/></svg><div><b>Email</b>hello@velim.example</div></div>
    <div class="f-item" style="top:137px"><svg width="12" height="13" viewBox="0 0 24 26"><path fill="#fff" d="M12 0a9 9 0 00-9 9c0 7 9 17 9 17s9-10 9-17a9 9 0 00-9-9zm0 12.5a3.5 3.5 0 110-7 3.5 3.5 0 010 7z"/></svg><div><b>Location</b>651 ,Lorem ipsum dolor sit amet,<br>consectetur adipiscing.</div></div>
  </div>

  <div class="abs f-col f-links" style="left:667px;top:1928px;width:150px">
    <h4>Company</h4>
    <div style="top:44px">Home</div>
    <div style="top:68px">About us</div>
    <div style="top:92px">Our Services</div>
    <div style="top:116px">Clients</div>
    <div style="top:140px">Contact us</div>
  </div>

  <div class="abs f-col" style="left:843px;top:1928px;width:215px">
    <h4>Stil have questios?</h4>
    <p style="margin-top:22px;font-size:12px;line-height:17.5px">Lorem ipsum dolor sit amet, consectet adipiscing elit, sed do eiusmod tempor incididunt ut labore et dolore.</p>
  </div>
  <div class="btn light" style="left:850px;top:2044px;width:137px;height:39px;font-size:14.5px">GET IN TOUCH</div>

  <div class="abs divider"></div>
  <div class="abs goup">
    <svg width="9" height="9" viewBox="0 0 10 10"><path d="M5 9V1M1.5 4.5L5 1l3.5 3.5" stroke="#fff" stroke-width="1.6" fill="none"/></svg>
    Go Up
  </div>
  <div class="abs copy">© 2023 Velim | All Rights Reserved</div>
  <div class="abs legal">Privacy Policy &nbsp;|&nbsp; Cookie Policy &nbsp;|&nbsp; Terms Of Services</div>

</div>
</body>
</html>
```